Website to design and sell sundials: www.gnomonvale.com

We have a website that creates a free paper sundial, we want to migrate from this not profit free website to a website where we will continue offering the free paper sundial model but We will also offer a manufactured sundial and sell it.
In order to understand the project, please visit:
http://www.gnomonvale.com/vertical/sundial.html and
http://www.torvel.net/landing/

The website user journey should be redesigned, including the phases that are,
select language
Show product give info
Creation/edit sundial (could be one or more phases)
View created sundial
Buy sundial.

May some of them could be combined or splitted, what It have more sense.

Requirements
Must have
• A description page user journey offering freemium paper sundial and physical sundial to sell.
• A sundial creation page for "free" paper sundial
• A result page for paper sundial
• A sell page for physical

```html
<!DOCTYPE html>
<html lang="en">
<head>
<meta charset="utf-8">
<title>GnomonVale – Create your Vertical Sundial</title>
<link href="https://fonts.googleapis.com/css2?family=Raleway:wght@400;500;600;700&family=Open+Sans:wght@400;600;700&display=swap" rel="stylesheet">
<style>
:root{
  --red:#c4161c;
  --red-band:#bf1410;
  --orange:#f0a830;
  --orange-dark:#de941c;
  --text:#2b2b2b;
  --muted:#666;
  --line:#d9d9d9;
  --footer:#2b2624;
  --footer-text:#d6d2d0;
  --white:#fff;
}
*{margin:0;padding:0;box-sizing:border-box}
html,body{width:1200px;height:2493px;overflow:hidden;background:var(--white)}
body{position:relative;font-family:"Open Sans",Arial,sans-serif;color:var(--text)}
.abs{position:absolute}
.top-rule{left:0;top:0;width:1200px;height:5px;background:var(--red)}
.brand{left:100px;top:38px;display:flex;align-items:center;gap:12px}
.brand-dot{width:22px;height:22px;border-radius:50%;background:var(--red)}
.brand-name{font-family:"Raleway",sans-serif;font-weight:600;font-size:29px;color:var(--red)}
.utility{top:20px;font-family:"Raleway",sans-serif;font-size:14px;color:var(--text);display:flex;align-items:center;gap:8px}
.main-nav{top:60px;right:101px;display:flex;gap:34px;font-family:"Raleway",sans-serif;font-weight:600;font-size:14.5px}
.main-nav .active{color:var(--orange)}
.hero{left:0;top:93px;width:1200px;height:268px;background:radial-gradient(ellipse at 55% 75%,#8b8580 0%,#6f6a66 45%,#5b5654 100%)}
.hero-title{left:0;top:178px;width:1200px;text-align:center;font-family:"Raleway",sans-serif;font-weight:700;font-size:68px;color:var(--white);text-shadow:0 2px 6px rgba(0,0,0,.35)}
.section-title{font-family:"Raleway",sans-serif;font-weight:600;font-size:24px;color:#222;letter-spacing:.3px}
.lead{left:98px;top:458px;font-size:13px;line-height:23px;color:var(--muted)}
.field{border:1px solid var(--line);background:var(--white)}
.btn{background:linear-gradient(var(--orange),var(--orange-dark));color:var(--white);font-family:"Raleway",sans-serif;font-weight:700;border-radius:4px;display:flex;align-items:center;justify-content:center;box-shadow:0 2px 0 #c5821a}
.map{left:98px;top:610px;width:1003px;height:420px;background:linear-gradient(160deg,#4f6a8a 0%,#b99e74 25%,#c9ad80 50%,#a88e68 75%,#8d7a63 100%)}
.face-diagram{left:98px;top:1200px;width:320px;height:186px;background:radial-gradient(ellipse at 62% 48%,#3a3a3a 0%,#8a8a8a 38%,#f2f2f2 72%,#fff 100%)}
.label{font-family:"Raleway",sans-serif;font-weight:600;font-size:15px;color:#333}
.divider{left:98px;top:1418px;width:1003px;height:1px;background:var(--line)}
.option-photo{border:1px solid var(--line);padding:4px;background:var(--white)}
.option-photo div{width:100%;height:100%}
.radio{width:19px;height:19px;border:1px solid #bbb;border-radius:50%;background:var(--white);display:inline-block}
.radio.on{background:radial-gradient(circle,var(--orange) 0 4px,#fff 5px)}
.box{width:17px;height:17px;border:1px solid #bbb;background:var(--white);display:inline-block}
.opt-label{font-family:"Raleway",sans-serif;font-weight:700;font-size:13.5px;color:#222}
.small{font-size:13px;color:#555}
.newsletter{left:0;top:2112px;width:1200px;height:85px;background:var(--red-band)}
.footer{left:0;top:2197px;width:1200px;height:296px;background:var(--footer)}
.foot-head{font-family:"Raleway",sans-serif;font-weight:700;font-size:14.5px;color:var(--white);letter-spacing:.3px}
.foot-list{list-style:none;font-size:12px;line-height:22.5px;color:var(--footer-text)}
.foot-list.u li{text-decoration:underline}
.foot-text{font-size:12px;line-height:20px;color:var(--footer-text)}
.card{width:38px;height:22px;border-radius:2px;display:inline-block;margin-right:5px}
.social{width:15px;height:15px;border-radius:2px;background:var(--white);display:inline-block;margin-left:4px}
</style>
</head>
<body>
<div class="abs top-rule"></div>

<header>
  <div class="abs brand"><span class="brand-dot"></span><span class="brand-name">GnomonVale.com</span></div>
  <div class="abs utility" style="left:880px">
    <svg width="40" height="20" viewBox="0 0 40 20"><path d="M3 8l8-5 9 3 8-4 9 5-6 6-8-2-6 7-8-4-6 2z" fill="#f0a830"/></svg>Language
  </div>
  <div class="abs utility" style="left:1015px">
    <svg width="28" height="24" viewBox="0 0 28 24"><path d="M2 3h5l3 13h13l3-9H9" fill="none" stroke="#f0a830" stroke-width="2.4"/><circle cx="12" cy="21" r="2" fill="#f0a830"/><circle cx="22" cy="21" r="2" fill="#f0a830"/></svg>Cart (0)
  </div>
  <nav class="abs main-nav">
    <span class="active">Home</span><span>About Us</span><span>Products</span><span>Shop</span><span>Blog</span><span>News</span><span>Contact Us</span>
    <svg width="15" height="15" viewBox="0 0 15 15" style="margin-left:-8px;margin-top:2px"><circle cx="6" cy="6" r="4.5" fill="none" stroke="#222" stroke-width="2"/><path d="M9.5 9.5l4 4" stroke="#222" stroke-width="2.2"/></svg>
  </nav>
</header>

<section class="abs hero" role="img" aria-label="Photograph of a large horizontal sundial with a tall gnomon"></section>
<h1 class="abs hero-title">Create your Vertical Sundial</h1>
<svg class="abs" style="left:66px;top:212px" width="16" height="26" viewBox="0 0 16 26"><path d="M13 2L3 13l10 11" fill="none" stroke="#fff" stroke-width="3"/></svg>
<svg class="abs" style="left:1118px;top:212px" width="16" height="26" viewBox="0 0 16 26"><path d="M3 2l10 11L3 24" fill="none" stroke="#fff" stroke-width="3"/></svg>

<main>
  <h2 class="abs section-title" style="left:98px;top:408px">SUNDIAL LOCATION</h2>
  <p class="abs lead">Select the location where you want to place your paper sundial, mark a line along building wall where you want to put it.<br>Write your address and press Go! (e.g. Picadilly circus, london, UK)</p>
  <div class="abs field" style="left:98px;top:528px;width:910px;height:49px"></div>
  <div class="abs btn" style="left:1022px;top:529px;width:77px;height:48px;font-size:15px">GO</div>

  <div class="abs map" role="img" aria-label="Satellite map of Central Asia for choosing the sundial location"></div>

  <span class="abs label" style="left:98px;top:1066px">Longitude&nbsp;:</span>
  <div class="abs field" style="left:206px;top:1057px;width:194px;height:37px"></div>
  <span class="abs label" style="left:432px;top:1066px">Latitude&nbsp;:</span>
  <div class="abs field" style="left:528px;top:1057px;width:194px;height:37px"></div>
  <span class="abs label" style="left:756px;top:1066px">Wall declination&nbsp;:</span>
  <div class="abs field" style="left:904px;top:1057px;width:196px;height:37px"></div>

  <span class="abs label" style="left:98px;top:1136px">Now select the face of the building&nbsp;:</span>
  <div class="abs field" style="left:400px;top:1128px;width:91px;height:36px;display:flex">
    <span style="flex:1;padding:7px 0 0 24px;font-size:15px">A</span>
    <span style="width:36px;background:#eee;border-left:1px solid var(--line);display:flex;align-items:center;justify-content:center"><svg width="10" height="6"><path d="M0 0h10L5 6z" fill="#777"/></svg></span>
  </div>

  <div class="abs face-diagram" role="img" aria-label="Building footprint diagram with north arrow, showing faces A to D and the selected wall"></div>

  <div class="abs divider"></div>

  <h2 class="abs section-title" style="left:98px;top:1452px">SUNDIAL OPTIONS</h2>
  <div class="abs option-photo" style="left:98px;top:1504px;width:252px;height:212px"><div role="img" aria-label="Paper sundial fixed to a brick wall" style="background:linear-gradient(90deg,#7a5b48,#9a6f55 40%,#e8eaec 45%,#dfe2e4 65%,#8a624c 70%,#6f5040)"></div></div>
  <div class="abs option-photo" style="left:367px;top:1504px;width:253px;height:212px"><div role="img" aria-label="Paper sundial taped to a window pane" style="background:linear-gradient(90deg,#2f2a25 0 20%,#c9bfb2 20%,#e0d6c8 60%,#9a8b7a 100%)"></div></div>
  <span class="abs radio on" style="left:98px;top:1733px"></span><span class="abs opt-label" style="left:130px;top:1734px">WALL SUNDIAL</span>
  <span class="abs radio" style="left:367px;top:1733px"></span><span class="abs opt-label" style="left:399px;top:1734px">WINDOW SUNDIAL</span>

  <span class="abs label" style="left:98px;top:1792px">Banner&nbsp;:</span>
  <div class="abs field" style="left:206px;top:1783px;width:894px;height:39px"></div>

  <span class="abs label" style="left:98px;top:1848px">Time&nbsp;:</span>
  <span class="abs radio on" style="left:206px;top:1848px"></span><span class="abs small" style="left:249px;top:1849px">Solar Time</span>
  <span class="abs radio" style="left:360px;top:1848px"></span><span class="abs small" style="left:404px;top:1849px">Civil Time</span>

  <span class="abs label" style="left:98px;top:1894px">Time&nbsp;:</span>
  <span class="abs box" style="left:207px;top:1895px"></span><span class="abs small" style="left:249px;top:1894px">Daylight Saving Time</span>
  <span class="abs box" style="left:422px;top:1895px"></span><span class="abs small" style="left:460px;top:1894px">Equation of time</span>

  <span class="abs label" style="left:98px;top:1956px">Timezone&nbsp;:</span>
  <div class="abs field" style="left:206px;top:1946px;width:894px;height:39px;display:flex">
    <span style="flex:1;padding:10px 0 0 18px;font-size:13px;color:#555">(GMT+11) Solomon Islands, New Caledonia</span>
    <span style="width:50px;background:#f3f3f3;border-left:1px solid var(--line);display:flex;align-items:center;justify-content:center"><svg width="10" height="6"><path d="M0 0h10L5 6z" fill="#777"/></svg></span>
  </div>

  <div class="abs btn" style="left:98px;top:2014px;width:176px;height:44px;font-size:14px">CREATE SUNDIAL</div>
</main>

<section class="abs newsletter">
  <svg class="abs" style="left:98px;top:24px" width="44" height="36" viewBox="0 0 44 36"><path d="M2 12L30 2l12 22-28 10z" fill="#fff"/><path d="M2 12l22 8 18 4" fill="none" stroke="#bf1410" stroke-width="2"/></svg>
  <div class="abs" style="left:163px;top:22px;color:#fff;font-family:'Raleway',sans-serif;font-weight:600;font-size:13px;letter-spacing:.5px">NEWSLETTER</div>
  <div class="abs" style="left:163px;top:40px;color:#fff;font-family:'Raleway',sans-serif;font-weight:600;font-size:20px">SUBSCRIPTION</div>
  <div class="abs" style="left:347px;top:22px;width:623px;height:37px;background:#fff;padding:11px 0 0 28px;font-size:11px;color:#888">ENTER EMAIL ADDRESS</div>
  <div class="abs" style="left:987px;top:20px;width:115px;height:41px;border:2px solid #fff;color:#fff;font-family:'Raleway',sans-serif;font-weight:700;font-size:14px;display:flex;align-items:center;justify-content:center">SUBSCRIBE</div>
</section>

<footer class="abs footer">
  <div class="abs" style="left:92px;top:54px;display:flex;align-items:center;gap:8px"><span style="width:14px;height:14px;border-radius:50%;background:#fff"></span><span style="font-family:'Raleway',sans-serif;font-weight:600;font-size:20px;color:#fff">GnomonVale.com</span></div>
  <p class="abs foot-text" style="left:100px;top:94px;width:235px">At vero eos et accusamus et iusto odio dignissimos ducimus qui blanditiis pra esentium voluptatum delen</p>
  <div class="abs" style="left:100px;top:175px">
    <span class="card" style="background:#e8e8e8"></span><span class="card" style="background:#f4f4f4"></span><span class="card" style="background:#e05a2a"></span><span class="card" style="background:#ececec"></span><span class="card" style="background:#3a72b8"></span>
  </div>

  <h3 class="abs foot-head" style="left:376px;top:36px">QUICK LINKS</h3>
  <ul class="abs foot-list u" style="left:376px;top:72px"><li>Contact</li><li>FAQ</li><li>Delivery</li><li>Returns</li><li>Track Orders</li><li>Subscribe</li></ul>

  <h3 class="abs foot-head" style="left:562px;top:36px">EXTRAS</h3>
  <ul class="abs foot-list" style="left:562px;top:72px"><li>Specials</li><li>New products</li><li>Top sellers</li><li>Our stores</li><li>Contact us</li><li>About us</li></ul>

  <h3 class="abs foot-head" style="left:725px;top:36px">MY ACCOUNT</h3>
  <ul class="abs foot-list" style="left:725px;top:72px"><li>Delivery Information</li><li>Privacy Policy</li><li>Returns Policy</li><li>Terms and Conditions</li><li>FAQs</li></ul>

  <h3 class="abs foot-head" style="left:940px;top:36px">CONTACT US</h3>
  <svg class="abs" style="left:940px;top:80px" width="10" height="14" viewBox="0 0 10 14"><path d="M5 14C1 8 0 6.5 0 5a5 5 0 0110 0c0 1.5-1 3-5 9z" fill="#fff"/><circle cx="5" cy="5" r="1.8" fill="#2b2624"/></svg>
  <p class="abs foot-text" style="left:967px;top:74px">218 Harbor Lane<br>Portside, CA 90210</p>
  <svg class="abs" style="left:940px;top:143px" width="12" height="12" viewBox="0 0 12 12"><path d="M2 0l3 3-1.5 2a7 7 0 003.5 3.5L9 7l3 3-2 2C5 12 0 7 0 2z" fill="#fff"/></svg>
  <p class="abs foot-text" style="left:967px;top:138px">1 555 010 010</p>
  <svg class="abs" style="left:940px;top:186px" width="13" height="10" viewBox="0 0 13 10"><rect width="13" height="10" fill="#fff"/><path d="M0 0l6.5 5L13 0" fill="none" stroke="#2b2624"/></svg>
  <p class="abs foot-text" style="left:969px;top:181px;text-decoration:underline">info@gnomonvale.com</p>

  <p class="abs foot-text" style="left:100px;top:250px;font-size:11.5px">Copyrights © 2016, GnomonVale. All Rights Reserved</p>
  <div class="abs foot-text" style="left:893px;top:248px;display:flex;align-items:center">Follow us on :&nbsp;<span class="social"></span><span class="social"></span><span class="social"></span><span class="social"></span><span class="social"></span><span class="social"></span></div>
</footer>
</body>
</html>
```